business card design for a plumbing contractor

i need a double business card for a plumbing business, our initial service is residential Sewer Drain Cleaning.

Target Market(s)

other plumbing Business

Industry/Entity Type

Plumbing

Contact Information for Business Card

www.PipeworksTopMark.example- 5307218394-

Font styles to use
Serif

Colors
ec1f27
0455a3

```html
<!DOCTYPE html>
<html lang="en">
<head>
<meta charset="utf-8">
<title>Kestrel Drain Co — Business Card</title>
<link rel="stylesheet" href="https://fonts.googleapis.com/css2?family=Roboto+Condensed:wght@400;700&display=swap">
<style>
  :root {
    --brand-red: #e03a33;
    --paper: #f4f4f3;
    --ink-grey: #8a8680;
    --white: #ffffff;
    --stage: #e6e3df;
  }
  * { box-sizing: border-box; margin: 0; padding: 0; }
  html, body { width: 1200px; height: 886px; overflow: hidden; }
  body {
    background: var(--stage);
    font-family: "Roboto Condensed", Arial, sans-serif;
    display: flex; align-items: center; justify-content: center; gap: 60px;
  }
  .card {
    width: 520px; height: 297px; border-radius: 18px; position: relative; overflow: hidden;
    box-shadow: 0 6px 18px rgba(0,0,0,.18);
  }

  /* Front */
  .card-front { background: var(--paper); }
  .front-brand {
    position: absolute; left: 44px; top: 34px;
    display: flex; align-items: center; gap: 18px;
  }
  .brand-name {
    font-weight: 700; font-size: 46px; line-height: .92; color: var(--ink-grey); letter-spacing: -.5px;
  }
  .brand-square { width: 30px; height: 30px; background: var(--brand-red); flex: none; }
  .front-band {
    position: absolute; left: 0; right: 0; top: 166px; height: 94px;
    background: var(--brand-red); color: var(--white);
    display: flex; justify-content: space-between; align-items: center;
    padding: 0 26px 0 24px;
  }
  .contact-list { list-style: none; font-size: 13px; line-height: 1.5; }
  .contact-list li { display: flex; align-items: center; gap: 10px; white-space: nowrap; }
  .contact-list svg { width: 11px; height: 11px; flex: none; }
  .person { text-align: right; align-self: flex-start; margin-top: 14px; }
  .person-name { font-weight: 700; font-size: 21px; letter-spacing: .3px; line-height: 1.1; }
  .person-title { font-size: 15px; line-height: 1.2; }

  /* Back */
  .card-back { background: var(--brand-red); color: var(--white); }
  .back-brand {
    position: absolute; left: 0; right: 0; top: 92px;
    display: flex; align-items: center; justify-content: center; gap: 18px;
  }
  .back-brand .brand-name { color: var(--white); font-size: 48px; }
  .back-brand .brand-square { background: var(--white); width: 32px; height: 32px; }
  .services {
    position: absolute; left: 0; right: 0; bottom: 30px; text-align center;
    text-align: center; font-size: 14px; letter-spacing: .3px;
  }
</style>
</head>
<body>
  <section class="card card-front" aria-label="Business card front">
    <div class="front-brand">
      <span class="brand-name">Kestrel<br>Drain Co</span>
      <span class="brand-square"></span>
    </div>
    <div class="front-band">
      <ul class="contact-list">
        <li>
          <svg viewBox="0 0 12 12" fill="currentColor"><path d="M2.5 1 4.3 1 5 3.6 3.9 4.6a6.5 6.5 0 0 0 3.5 3.5L8.4 7 11 7.7V9.5c0 .8-.7 1.5-1.5 1.5A8.5 8.5 0 0 1 1 2.5C1 1.7 1.7 1 2.5 1Z"/></svg>
          5307218394
        </li>
        <li>
          <svg viewBox="0 0 12 12" fill="none" stroke="currentColor" stroke-width="1.3"><rect x="1" y="2.5" width="10" height="7"/><path d="M1 2.5 6 6.5 11 2.5"/></svg>
          Dispatcher@PipeworksTopMark.example
        </li>
        <li>
          <svg viewBox="0 0 12 12" fill="none" stroke="currentColor" stroke-width="1.1"><circle cx="6" cy="6" r="5"/><path d="M1 6h10M6 1c-2.5 3-2.5 7 0 10M6 1c2.5 3 2.5 7 0 10"/></svg>
          www.PipeworksTopMark.example
        </li>
      </ul>
      <div class="person">
        <div class="person-name">DALE HARPER</div>
        <div class="person-title">CEO/FOUNDER</div>
      </div>
    </div>
  </section>

  <section class="card card-back" aria-label="Business card back">
    <div class="back-brand">
      <span class="brand-name">Kestrel<br>Drain Co</span>
      <span class="brand-square"></span>
    </div>
    <p class="services">Sewer Drain Cleaning &nbsp;|&nbsp; Trenchless Pipe Installs</p>
  </section>
</body>
</html>
```